Postcard for Antique Furniture Restorer

My business is to restore antique furniture. I am based in Sydney, Australia.

I will be using this postcard to promote my business.
I will give it to customers like a With Compliments card.

Sometimes I will be writing information on the back of the card.

Design for Postcard Size eg 148 X 105mm

Front of card:

Attached are images of Antique furniture - please use ONLY 1 of the 3 images.
Deep etch the image on a white or cream background.

On front of card add these words:
Grainward Keepsakes
antique furniture restoration

Antiques travel through time, seeing generations of families
Through time they remain - they tell a continuing story
Be part of the journey

Back of postcard:
(leave space for notes to be handwritten)

Add these words:

Grainward Keepsakes
Corin Maddaford
mobile 0473 582 316
www.oakmendcraftery.com.au

Industry/Entity Type

Business

Font styles to use
Serif
Sans Serif

Colors
fefdec
ffffff

Requirements
Must have
• Use only 1 image. Image must be deep etched.

```html
<!DOCTYPE html>
<html lang="en">
<head>
<meta charset="utf-8">
<title>Grainward Keepsakes – Postcard</title>
<link href="https://fonts.googleapis.com/css2?family=Crimson+Text:ital,wght@0,400;0,600;1,400;1,600;1,700&display=swap" rel="stylesheet">
<style>
  :root {
    --stage: #e4e4e4;
    --cream: #fbfbec;
    --paper: #fefdf3;
    --maroon: #531417;
    --muted: #8f7a6c;
    --rule: #d9d3c6;
    --tan-dark: #b98a5e;
    --tan-light: #f3dfc7;
    --ornament: #e8d6bd;
    --wood: #6b2a14;
  }
  * { box-sizing: border-box; margin: 0; padding: 0; }
  html, body { width: 1200px; height: 560px; overflow: hidden; }
  body { background: var(--stage); position: relative; font-family: "Crimson Text", serif; }

  .card {
    position: absolute;
    top: 94px;
    width: 540px;
    height: 384px;
    background: var(--cream);
    overflow: hidden;
  }
  .card--front { left: 46px; }
  .card--back { left: 618px; }

  .ribbon { position: absolute; left: 0; top: 0; }
  .ribbon__name {
    position: absolute; left: 74px; width: 392px; top: 24px;
    text-align: center;
    font: 600 27px/1 "Crimson Text", serif;
    color: var(--maroon);
  }
  .ribbon__tagline {
    position: absolute; left: 74px; width: 392px; top: 55px;
    text-align: center;
    font: 400 13px/1 "Crimson Text", serif;
    letter-spacing: 0.14em;
    text-transform: uppercase;
    color: var(--maroon);
  }

  .ornament {
    position: absolute;
    background: radial-gradient(ellipse at center, var(--ornament) 0%, rgba(232,214,189,0.35) 55%, rgba(232,214,189,0) 75%);
  }
  .ornament--front-left { left: 0; top: 258px; width: 120px; height: 140px; }
  .ornament--front-right { left: 420px; top: 258px; width: 120px; height: 140px; }

  .product-photo {
    position: absolute; left: 113px; top: 80px;
    width: 319px; height: 228px;
    border-radius: 4px;
    background: linear-gradient(180deg, #6f9a3e 0%, #7d3519 30%, var(--wood) 65%, #bcb8b1 100%);
    box-shadow: 0 1px 4px rgba(0,0,0,0.25);
  }

  .motto {
    position: absolute; left: 0; right: 0; top: 322px;
    text-align: center;
    font: italic 400 14px/16px "Crimson Text", serif;
    color: var(--maroon);
  }
  .motto__call { font-weight: 700; }

  .ornament--back-top { left: 42px; top: 46px; width: 216px; height: 92px; }
  .ornament--back-bottom { left: 42px; top: 238px; width: 216px; height: 92px; }

  .band {
    position: absolute; left: 0; top: 156px;
    width: 288px; height: 60px;
    background: linear-gradient(90deg, var(--tan-dark) 0%, var(--tan-light) 55%, var(--tan-dark) 100%);
  }
  .band__name {
    position: absolute; left: 0; right: 0; top: 9px;
    text-align: center;
    font: 600 24px/1 "Crimson Text", serif;
    color: var(--maroon);
  }
  .band__tagline {
    position: absolute; left: 0; right: 0; top: 37px;
    text-align: center;
    font: 400 11px/1 "Crimson Text", serif;
    letter-spacing: 0.14em;
    text-transform: uppercase;
    color: var(--maroon);
  }

  .note-panel {
    position: absolute; left: 288px; top: 18px;
    width: 234px; height: 346px;
    background: var(--paper);
    box-shadow: 0 0 4px rgba(0,0,0,0.18);
  }
  .note-panel__label {
    position: absolute; left: 0; right: 0; top: 36px;
    text-align: center;
    font: 400 13px/1 "Crimson Text", serif;
    color: var(--muted);
  }
  .note-panel__lines {
    position: absolute; left: 12px; right: 12px; top: 66px;
    height: 182px;
    background: repeating-linear-gradient(180deg, transparent 0 13px, var(--rule) 13px 14px);
  }
  .contact {
    position: absolute; left: 0; right: 0; top: 272px;
    text-align: center;
    color: var(--maroon);
  }
  .contact__name { font-size: 16px; font-weight: 700; font-style: italic; line-height: 19px; }
  .contact__phone { font-size: 17px; font-weight: 600; line-height: 19px; }
  .contact__web { font-size: 13px; font-weight: 600; line-height: 18px; }
</style>
</head>
<body>

<section class="card card--front">
  <div class="ornament ornament--front-left" role="img" aria-label="Decorative flourish scrollwork"></div>
  <div class="ornament ornament--front-right" role="img" aria-label="Decorative flourish scrollwork"></div>

  <svg class="ribbon" width="540" height="120" viewBox="0 0 540 120" aria-hidden="true">
    <defs>
      <linearGradient id="ribbonFace" x1="0" x2="1" y1="0" y2="0">
        <stop offset="0" stop-color="#b98a5e"/>
        <stop offset="0.5" stop-color="#f3dfc7"/>
        <stop offset="1" stop-color="#b98a5e"/>
      </linearGradient>
    </defs>
    <polygon points="45,55 120,55 120,110 45,110 62,82" fill="#b98a5e"/>
    <polygon points="495,55 420,55 420,110 495,110 478,82" fill="#b98a5e"/>
    <polygon points="90,80 120,80 120,96" fill="#7e5635"/>
    <polygon points="450,80 420,80 420,96" fill="#7e5635"/>
    <rect x="74" y="22" width="392" height="58" fill="url(#ribbonFace)"/>
  </svg>
  <div class="ribbon__name">Grainward Keepsakes</div>
  <div class="ribbon__tagline">Antique Furniture Restoration</div>

  <div class="product-photo" role="img" aria-label="Deep-etched photo of a restored mahogany chest of drawers"></div>

  <p class="motto">
    Antiques travel through time, seeing generations of families<br>
    Through time they remain - they tell a continuing story<br>
    <span class="motto__call">Be part of the journey</span>
  </p>
</section>

<section class="card card--back">
  <div class="ornament ornament--back-top" role="img" aria-label="Symmetrical floral ornament"></div>
  <div class="ornament ornament--back-bottom" role="img" aria-label="Symmetrical floral ornament"></div>

  <div class="band">
    <div class="band__name">Grainward Keepsakes</div>
    <div class="band__tagline">Antique Furniture Restoration</div>
  </div>

  <div class="note-panel">
    <div class="note-panel__label">Note:</div>
    <div class="note-panel__lines"></div>
    <div class="contact">
      <div class="contact__name">Corin Maddaford</div>
      <div class="contact__phone">0473 582 316</div>
      <div class="contact__web">www.oakmendcraftery.com.au</div>
    </div>
  </div>
</section>

</body>
</html>
```